Law Firm Header Revision

Task: Redesign my law firm Word document header (modern, succinct, logo-first, easy address updates)

I need you to revise and modernize my Microsoft Word document header for Law Office of Bram Holcott, PLLC. The result should look professional and clean on letters (including Letters of Protection), with the logo as the main focus and the text kept succinct.

Goals:
1. Create a modern, minimal header that feels premium and uncluttered.
Make the logo the most visually dominant element.
Reduce the visual weight of the contact/address block so it doesn’t distract from the document.
Make the address easy to change later (I’m moving offices soon) while keeping the same header design.

2. Content to include (keep all info accurate):
Law Office of Bram Holcott, PLLC
615 Pemberly St. Ste #300-214, Houston, TX 77002
Office: 832.555.0143
Direct: 713.555.0187
Fax: 832.555.0129
Bholcottlaw.com

3. Layout requirements:
Provide 3 header style options:
Logo left + contact info right
Centered logo + single concise contact line below
Logo left + firm name prominent + minimal contact line
The primary line near the logo should be minimal (preferably website + main office phone).
The address should be easy to update in one place without redesigning the header. Prefer either:
Move the full address to the footer, or
Put the address in a single dedicated line/block so I can edit it once and keep the layout unchanged.
4. Build constraints:
Must be achievable using standard Microsoft Word tools only (header/footer, tables, alignment, fonts, spacing). No advanced graphics software.
Provide exact header text, plus step-by-step Word instructions for each option:
Font recommendations + sizes
Alignment
Spacing
Table setup (if used)
How to keep it consistent across pages

5. Deliverable:
For each of the 3 options, provide:
The exact header content (with line breaks)
Formatting specs (fonts, sizes, spacing)
Word build steps so I can recreate it reliably and keep the logo as the focal point.

```html
<!DOCTYPE html>
<html lang="en">
<head>
<meta charset="utf-8">
<title>Bram Holcott Law – Letterhead Options</title>
<link rel="stylesheet" href="https://fonts.googleapis.com/css2?family=Barlow:wght@400;500;600&display=swap">
<style>
  :root {
    --board: #2b2b2b;
    --paper: #f6f6f6;
    --paper-light: #fbfbfb;
    --navy: #0c1427;
    --ink: #1b2233;
    --muted: #6b6f78;
    --white: #ffffff;
  }
  * { box-sizing: border-box; margin: 0; padding: 0; }
  html, body { width: 1031px; height: 1200px; overflow: hidden; background: var(--board); }
  body { position: relative; font-family: "Barlow", Arial, sans-serif; }

  .sheet {
    position: absolute;
    width: 680px; height: 880px;
    transform-origin: 0 0;
    transform: scale(0.5794);
    background: linear-gradient(160deg, var(--paper-light), var(--paper));
    box-shadow: 0 10px 30px rgba(0,0,0,0.45);
    overflow: hidden;
  }
  .sheet--left-top { left: 90px; top: 58px; }
  .sheet--right-top { left: 547px; top: 58px; }
  .sheet--left-bottom { left: 90px; top: 632px; }

  /* Wordmark */
  .wordmark { position: absolute; display: flex; align-items: center; gap: 10px; }
  .wordmark__mark { width: 58px; height: 58px; background: var(--navy); }
  .wordmark__name { font-size: 34px; font-weight: 500; color: var(--navy); letter-spacing: 0.5px; line-height: 1; }

  /* Header option 1 */
  .header-rule { position: absolute; left: 0; right: 0; height: 2px; background: var(--navy); }
  .header-rule--thin { height: 1px; }
  .contact-stack { position: absolute; right: 37px; top: 28px; text-align: right; font-size: 13px; line-height: 24px; color: var(--ink); }
  .contact-stack .value { color: var(--muted); }

  /* Header option 2 */
  .header-bar {
    position: absolute; left: 0; right: 0; top: 98px; height: 35px;
    background: var(--navy); color: var(--white);
    display: flex; align-items: center; justify-content: center; gap: 22px;
    font-size: 13px;
  }
  .header-bar .divider { width: 1px; height: 14px; background: var(--white); }

  /* Header option 3 */
  .firm-tab {
    position: absolute; left: 36px; top: 0; width: 174px; height: 170px;
    background: var(--navy);
    border-radius: 0 0 87px 87px / 0 0 22px 22px;
    display: flex; flex-direction: column; align-items: center;
    padding-top: 32px;
  }
  .firm-tab__mark { width: 46px; height: 46px; background: var(--white); margin-bottom: 28px; }
  .firm-tab__name { color: var(--white); font-size: 13.5px; font-weight: 500; text-align: center; line-height: 18px; text-transform: uppercase; }

  /* Footer */
  .footer-art { position: absolute; left: 0; top: 0; width: 680px; height: 880px; }
  .footer-contacts {
    position: absolute; left: 0; right: 0; top: 728px;
    display: flex; flex-direction: column; align-items: center;
    color: var(--white); font-size: 13px; line-height: 24.3px;
  }
  .footer-contacts .row { display: flex; align-items: center; gap: 10px; }
  .footer-contacts svg { width: 12px; height: 12px; fill: var(--white); }
  .doc-strip {
    position: absolute; left: 70px; width: 540px; top: 840px; height: 28px;
    background: var(--white); border-radius: 14px;
    display: flex; justify-content: space-between; align-items: center;
    padding: 0 24px; font-size: 11px; color: var(--ink);
  }
</style>
</head>
<body>

<!-- Option 1: logo left, contact right -->
<section class="sheet sheet--left-top">
  <div class="wordmark" style="left:36px; top:30px;">
    <span class="wordmark__mark"></span>
    <span class="wordmark__name">BRAM HOLCOTT</span>
  </div>
  <div class="contact-stack">
    <div>Law Office of Bram Holcott, PLLC</div>
    <div>Website: <span class="value">Bholcottlaw.com</span></div>
    <div>Office: <span class="value">832.555.0143</span></div>
  </div>
  <div class="header-rule" style="top:112px;"></div>
  <div class="header-rule header-rule--thin" style="top:116px;"></div>

  <svg class="footer-art" viewBox="0 0 680 880" aria-hidden="true">
    <path d="M0 790 C130 735 240 697 340 697 C440 697 550 735 680 790 L680 880 L0 880 Z" fill="var(--navy)"/>
    <path d="M0 815 Q100 760 200 718" fill="none" stroke="var(--white)" stroke-width="3"/>
    <path d="M680 815 Q580 760 480 718" fill="none" stroke="var(--white)" stroke-width="3"/>
  </svg>
  <div class="footer-contacts">
    <div class="row"><svg viewBox="0 0 12 12"><rect x="0" y="0" width="12" height="12" rx="2"/></svg>Direct:&nbsp; 713.555.0187</div>
    <div class="row"><svg viewBox="0 0 12 12"><rect x="1" y="3" width="10" height="9" rx="1"/><rect x="3" y="0" width="6" height="4"/></svg>Fax Number:&nbsp; 832.555.0129</div>
    <div class="row"><svg viewBox="0 0 12 12"><path d="M0 2h12v8H0z"/></svg>Email Address:&nbsp; Bholcottlaw.com</div>
    <div class="row"><svg viewBox="0 0 12 12"><path d="M6 0a4 4 0 0 1 4 4c0 3-4 8-4 8S2 7 2 4a4 4 0 0 1 4-4z"/></svg>615 Pemberly St. Ste #300-214, Houston, TX 77002</div>
  </div>
  <div class="doc-strip"><span>Letter Of Protection</span><span>Page 01</span></div>
</section>

<!-- Option 2: centred logo, single contact line -->
<section class="sheet sheet--right-top">
  <div class="wordmark" style="left:210px; top:20px;">
    <span class="wordmark__mark"></span>
    <span class="wordmark__name">BRAM HOLCOTT</span>
  </div>
  <div class="header-bar">
    <span>Website:&nbsp; www.Bholcottlaw.com</span>
    <span class="divider"></span>
    <span>Office:&nbsp; 832.555.0143</span>
  </div>
  <div class="header-rule" style="top:135px;"></div>

  <svg class="footer-art" viewBox="0 0 680 880" aria-hidden="true">
    <path d="M0 790 C130 735 240 697 340 697 C440 697 550 735 680 790 L680 880 L0 880 Z" fill="var(--navy)"/>
    <path d="M0 815 Q100 760 200 718" fill="none" stroke="var(--white)" stroke-width="3"/>
    <path d="M680 815 Q580 760 480 718" fill="none" stroke="var(--white)" stroke-width="3"/>
  </svg>
  <div class="footer-contacts">
    <div class="row"><svg viewBox="0 0 12 12"><rect x="0" y="0" width="12" height="12" rx="2"/></svg>Direct:&nbsp; 713.555.0187</div>
    <div class="row"><svg viewBox="0 0 12 12"><rect x="1" y="3" width="10" height="9" rx="1"/><rect x="3" y="0" width="6" height="4"/></svg>Fax Number:&nbsp; 832.555.0129</div>
    <div class="row"><svg viewBox="0 0 12 12"><path d="M0 2h12v8H0z"/></svg>Email Address:&nbsp; Bholcottlaw.com</div>
    <div class="row"><svg viewBox="0 0 12 12"><path d="M6 0a4 4 0 0 1 4 4c0 3-4 8-4 8S2 7 2 4a4 4 0 0 1 4-4z"/></svg>615 Pemberly St. Ste #300-214, Houston, TX 77002</div>
  </div>
  <div class="doc-strip"><span>Letter Of Protection</span><span>Page 01</span></div>
</section>

<!-- Option 3: logo tab + firm name, minimal contact -->
<section class="sheet sheet--left-bottom">
  <div class="firm-tab">
    <span class="firm-tab__mark"></span>
    <span class="firm-tab__name">Law Office of Bram<br>Holcott, PLLC</span>
  </div>
  <div class="contact-stack">
    <div>Website: <span class="value">Bholcottlaw.com</span></div>
    <div>Office: <span class="value">832.555.0143</span></div>
  </div>

  <svg class="footer-art" viewBox="0 0 680 880" aria-hidden="true">
    <path d="M0 790 C130 735 240 697 340 697 C440 697 550 735 680 790 L680 880 L0 880 Z" fill="var(--navy)"/>
    <path d="M0 815 Q100 760 200 718" fill="none" stroke="var(--white)" stroke-width="3"/>
    <path d="M680 815 Q580 760 480 718" fill="none" stroke="var(--white)" stroke-width="3"/>
  </svg>
  <div class="footer-contacts">
    <div class="row"><svg viewBox="0 0 12 12"><rect x="0" y="0" width="12" height="12" rx="2"/></svg>Direct:&nbsp; 713.555.0187</div>
    <div class="row"><svg viewBox="0 0 12 12"><rect x="1" y="3" width="10" height="9" rx="1"/><rect x="3" y="0" width="6" height="4"/></svg>Fax Number:&nbsp; 832.555.0129</div>
    <div class="row"><svg viewBox="0 0 12 12"><path d="M0 2h12v8H0z"/></svg>Email Address:&nbsp; Bholcottlaw.com</div>
    <div class="row"><svg viewBox="0 0 12 12"><path d="M6 0a4 4 0 0 1 4 4c0 3-4 8-4 8S2 7 2 4a4 4 0 0 1 4-4z"/></svg>615 Pemberly St. Ste #300-214, Houston, TX 77002</div>
  </div>
  <div class="doc-strip"><span>Letter Of Protection</span><span>Page 01</span></div>
</section>

</body>
</html>
```